Health Care Company with Logo Needs Business Cards designed

We are a luxury behavioral health company looking for business cards design we already have a logo and are looking for someone to design a sophisticated luxurious looking business card. Please note that Card design should be captivating just like the logo and also encompass the logo color

Industry/Entity Type

Healthcare

Contact Information for Business Card

Logo,company name, tagline, my name and title, contact details, and physical address

```html
<!DOCTYPE html>
<html lang="en">
<head>
<meta charset="utf-8">
<title>Harbor Crest Behavioral Health – Business Card</title>
<link rel="stylesheet" href="https://fonts.googleapis.com/css2?family=Roboto+Condensed:wght@300;400;700&display=swap">
<style>
  :root {
    --page-bg: #e6e8eb;
    --card-dark: #050505;
    --card-mid: #1c1c1e;
    --card-light: #3a3a3c;
    --brand-purple: #6b3e92;
    --brand-blue: #2ea3dc;
    --brand-orange: #e8892c;
    --brand-green: #7cb342;
    --text-light: #e8e8e8;
    --text-soft: #c9c9cc;
  }
  * { margin: 0; padding: 0; box-sizing: border-box; }
  html, body {
    width: 1200px; height: 900px; overflow: hidden;
    background: var(--page-bg);
    font-family: "Roboto Condensed", "Arial Narrow", sans-serif;
  }
  .canvas {
    width: 1200px; height: 900px;
    display: flex; align-items: center; justify-content: center;
  }
  .business-card {
    position: relative;
    width: 1040px; height: 593px;
    border-radius: 4px;
    overflow: hidden;
    background:
      radial-gradient(ellipse at 10% 95%, var(--card-light) 0%, var(--card-mid) 35%, transparent 65%),
      linear-gradient(100deg, var(--card-mid) 0%, var(--card-dark) 55%, #111 100%);
    box-shadow: 0 18px 40px rgba(0,0,0,.25);
    color: var(--text-light);
  }
  .brand {
    position: absolute; left: 58px; top: 60px;
    display: flex; align-items: flex-start; gap: 24px;
  }
  .brand-square {
    width: 72px; height: 72px;
    background: var(--brand-orange);
    flex: none;
  }
  .brand-name {
    font-size: 50px; font-weight: 700; line-height: 1;
    color: var(--brand-purple);
    letter-spacing: .5px;
  }
  .brand-tagline {
    margin-top: 10px;
    font-size: 17px; font-weight: 700;
    letter-spacing: 3.4px;
    text-transform: uppercase;
    color: var(--brand-blue);
  }
  .person { position: absolute; left: 58px; top: 212px; }
  .person-name {
    font-size: 37px; font-weight: 700;
    text-transform: uppercase;
    color: var(--brand-blue);
    line-height: 1.1;
  }
  .person-title {
    margin-top: 6px;
    font-size: 27px; font-weight: 400;
    color: var(--text-light);
  }
  .address {
    position: absolute; left: 58px; top: 320px;
    font-style: normal;
    font-size: 27px; font-weight: 300; line-height: 38px;
    color: var(--text-soft);
  }
  .contact-list {
    position: absolute; left: 58px; top: 432px;
    list-style: none;
    font-size: 26px; font-weight: 300; line-height: 38px;
    color: var(--text-soft);
  }
  .contact-list li { display: flex; align-items: center; gap: 12px; }
  .contact-icon { width: 22px; height: 22px; flex: none; }
</style>
</head>
<body>
<main class="canvas">
  <article class="business-card">
    <header class="brand">
      <span class="brand-square" aria-hidden="true"></span>
      <div>
        <div class="brand-name">Harbor Crest Behavioral Health</div>
        <div class="brand-tagline">Committed to calm, care and renewal</div>
      </div>
    </header>

    <section class="person">
      <h1 class="person-name">Daniel Okafor</h1>
      <p class="person-title">President</p>
    </section>

    <address class="address">
      1820 Seabright Cove<br>
      Laguna Vista CA 92600
    </address>

    <ul class="contact-list">
      <li>
        <svg class="contact-icon" viewBox="0 0 24 24" aria-hidden="true">
          <path fill="var(--brand-orange)" d="M6.6 10.8a15.1 15.1 0 0 0 6.6 6.6l2.2-2.2a1 1 0 0 1 1-.25 11.4 11.4 0 0 0 3.6.57 1 1 0 0 1 1 1V20a1 1 0 0 1-1 1A17 17 0 0 1 3 4a1 1 0 0 1 1-1h3.5a1 1 0 0 1 1 1c0 1.250.2 2.450.57 3.570a1 1 0 0 1-.25 1z"/>
        </svg>
        555-014-2386
      </li>
      <li>
        <svg class="contact-icon" viewBox="0 0 24 24" aria-hidden="true">
          <rect x="2" y="5" width="20" height="14" rx="1.5" fill="var(--brand-green)"/>
          <path d="M3 6.5l9 6.5 9-6.5" fill="none" stroke="#1c1c1e" stroke-width="1.6"/>
        </svg>
        info@harborcresthealth.com
      </li>
      <li>
        <svg class="contact-icon" viewBox="0 0 24 24" aria-hidden="true">
          <g fill="none" stroke="var(--brand-blue)" stroke-width="1.8">
            <circle cx="12" cy="12" r="9"/>
            <ellipse cx="12" cy="12" rx="4" ry="9"/>
            <path d="M3 12h18"/>
          </g>
        </svg>
        www.harborcresthealth.com
      </li>
    </ul>
  </article>
</main>
</body>
</html>
```